Letter and Envelope Design For Harborline Realty

Please design a letter and an envelope incorporating our logo (See Attached). We are also launched a business card contest. Since we want them to match, please feel free to submit a design for both the business card and also the letter design and envelope.

Requirements
Must have
• The envelope, the letter and the business cards must match somehow connecting the designs. We want them to have something that holds them together besides the logo.

```html
<!DOCTYPE html>
<html lang="en">
<head>
<meta charset="utf-8">
<title>Harborline Realty Stationery</title>
<link href="https://fonts.googleapis.com/css2?family=Lato:wght@400;700&family=Open+Sans:wght@400;600&family=Kaushan+Script&display=swap" rel="stylesheet">
<style>
:root{
  --navy:#272f7e;
  --ink:#5d5e60;
  --heading:#1d4a6b;
  --stage:#bcbdc1;
  --paper:#ffffff;
  --paper-shade:#ececed;
  --rule:#d0d1d4;
}
*{margin:0;padding:0;box-sizing:border-box}
html,body{width:1200px;height:484px;overflow:hidden;background:var(--stage)}
.canvas{position:relative;width:1200px;height:484px;font-family:"Open Sans",sans-serif;color:var(--ink)}
.sheet{position:absolute;background:var(--paper);overflow:hidden}

/* brand lockup */
.brand{position:absolute;display:flex;flex-direction:column;align-items:center;color:var(--navy);font-family:"Lato",sans-serif;font-weight:700}
.brand-ring{border:2.5px solid var(--navy);border-radius:50%}
.brand-name{font-size:10px;letter-spacing:.6px;margin-top:4px;line-height:1}
.brand-sub{font-size:6px;letter-spacing:2.4px;display:flex;align-items:center;gap:5px;margin-top:2px;line-height:1}
.brand-sub::before,.brand-sub::after{content:"";width:20px;height:1px;background:var(--navy)}

/* letterhead */
.letter{top:38px;width:322px;height:417px;background:linear-gradient(180deg,var(--paper) 0%,var(--paper) 40%,var(--paper-shade) 100%)}
.letter.first{left:32px}
.letter.second{left:378px}
.letter .brand{left:26px;top:10px}
.letter .brand-ring{width:32px;height:32px}
.contact-list{position:absolute;list-style:none;font-size:5.2px;line-height:8px;color:var(--ink)}
.contact-list li{display:flex;align-items:center;gap:3px}
.contact-list svg{width:5px;height:5px;fill:var(--navy)}
.letter .contact-top{left:232px;top:25px;border-left:1px solid var(--rule);padding-left:4px}
.salutation{position:absolute;left:26px;top:94px;font-size:6.6px;font-weight:600;color:var(--heading)}
.body-copy{position:absolute;left:26px;top:110px;width:268px;font-size:5.7px;line-height:9.5px;text-align:justify}
.body-copy p{margin-bottom:7.5px}
.closing{position:absolute;left:26px;top:278px;font-size:7.4px}
.signature{position:absolute;left:26px;top:292px;font-family:"Kaushan Script",cursive;font-size:12px;color:var(--heading)}
.footer-rule{position:absolute;left:0;right:0;height:2px;background:var(--navy)}
.letter .footer-rule{top:401px}
.end-mark{position:absolute;display:flex;align-items:center;gap:3px;font-family:"Lato",sans-serif;font-weight:700;color:var(--navy);background:var(--paper);padding-left:3px}
.end-ring{border:2px solid var(--navy);border-radius:50%;background:var(--paper)}
.letter .end-mark{right:8px;top:390px;font-size:5px}
.letter .end-ring{width:24px;height:24px}
.footer-address{position:absolute;left:26px;top:406px;font-size:4.8px;display:flex;align-items:center;gap:3px}
.footer-address svg{width:5px;height:5px;fill:var(--navy)}
.letter .contact-bottom{left:26px;top:389px;display:flex;gap:8px}

/* envelopes */
.envelope-back{left:816px;top:26px;width:360px;height:162px;background:var(--paper)}
.flap-fill{position:absolute;left:0;top:0;width:360px;height:66px}
.envelope-back .brand{left:150px;top:9px}
.envelope-mid{left:790px;top:94px;width:360px;height:162px;border:1px solid var(--rule)}
.flap-line{position:absolute;left:0;top:0;width:360px;height:70px}
.envelope-mid .brand{left:150px;top:10px}
.flap-brand .brand-ring{width:32px;height:32px}
.flap-brand .brand-name{font-size:7px}
.envelope-back .brand{color:var(--paper)}
.envelope-back .brand-ring{border-color:var(--paper)}
.envelope-front{left:730px;top:166px;width:360px;height:162px;border:1px solid var(--rule)}
.envelope-front .brand{left:10px;top:10px}
.envelope-front .brand-ring{width:30px;height:30px}
.envelope-front .footer-address{left:10px;top:64px;font-size:6px;align-items:flex-start;line-height:9px}
.envelope-front .footer-address svg{width:6px;height:6px;margin-top:1.5px}
.envelope-front .footer-rule{top:145px}
.envelope-front .end-mark{right:14px;top:135px;font-size:5px}
.envelope-front .end-ring{width:22px;height:22px}
.web{position:absolute;font-family:"Lato",sans-serif;font-size:5.8px;letter-spacing:1.2px;color:var(--ink)}
.web strong{color:var(--navy)}
.envelope-front .web{left:14px;top:150px}

/* business cards */
.card-front{left:730px;top:348px;width:170px;height:97px}
.card-front .brand{left:6px;top:6px}
.card-front .brand-ring{width:24px;height:24px}
.card-front .brand-name{font-size:7.6px}
.card-front .brand-sub{font-size:4.8px}
.card-front .brand-sub::before,.card-front .brand-sub::after{width:14px}
.holder{position:absolute;right:7px;top:31px;text-align:right;line-height:1.15}
.holder-name{font-family:"Lato",sans-serif;font-weight:700;font-size:6.4px;color:var(--navy)}
.holder-role{font-size:5.2px}
.card-front .contact-bottom{left:7px;top:67px;font-size:4.4px;line-height:7px}
.card-front .footer-rule{top:84px;height:1.5px}
.card-front .footer-address{left:7px;top:87px;font-size:4.4px}
.card-front .end-mark{right:8px;top:74px;font-size:4px}
.card-front .end-ring{width:20px;height:20px}
.card-back{left:916px;top:348px;width:169px;height:97px;background:var(--navy)}
.card-back .brand{left:0;right:0;top:12px;color:var(--paper)}
.card-back .brand-ring{width:42px;height:42px;border-color:var(--paper);border-width:3px}
.card-back .brand-name{font-size:8px}
.card-back .web{left:0;right:0;top:84px;text-align:center;color:var(--paper);font-size:4.6px;display:flex;justify-content:center;align-items:center;gap:5px}
.card-back .web::before,.card-back .web::after{content:"";width:28px;height:.7px;background:var(--paper)}
</style>
</head>
<body>
<svg width="0" height="0" style="position:absolute">
  <symbol id="icon-phone" viewBox="0 0 10 10"><circle cx="5" cy="5" r="5"/><path d="M3 2.4l1 1-.5.8a4 4 0 0 0 2.3 2.3l.8-.5 1 1-.7.8C5 7.6 2.4 5 2.2 3.1z" fill="#fff"/></symbol>
  <symbol id="icon-mail" viewBox="0 0 10 10"><rect x="0" y="1.5" width="10" height="7" rx="1"/><path d="M.8 2.5L5 5.6l4.2-3.1" stroke="#fff" fill="none" stroke-width=".9"/></symbol>
  <symbol id="icon-web" viewBox="0 0 10 10"><circle cx="5" cy="5" r="5"/><path d="M1 5h8M5 1c-2 2.4-2 5.6 0 8M5 1c2 2.4 2 5.6 0 8" stroke="#fff" fill="none" stroke-width=".7"/></symbol>
  <symbol id="icon-pin" viewBox="0 0 10 10"><circle cx="5" cy="5" r="5"/><path d="M5 2.2a2 2 0 0 0-2 2c0 1.5 2 3.6 2 3.6s2-2.1 2-3.6a2 2 0 0 0-2-2z" fill="#fff"/></symbol>
</svg>

<main class="canvas">

  <section class="sheet letter first" aria-label="Letterhead with header contacts">
    <div class="brand"><span class="brand-ring"></span><span class="brand-name">HARBORLINE</span><span class="brand-sub">REALTY</span></div>
    <ul class="contact-list contact-top">
      <li><svg><use href="#icon-phone"/></svg>012-345-6789</li>
      <li><svg><use href="#icon-mail"/></svg>info@harborline.com</li>
      <li><svg><use href="#icon-web"/></svg>www.harborline.com</li>
    </ul>
    <p class="salutation">Dear Mr. Lorem,</p>
    <div class="body-copy">
      <p>Lorem ipsum dolor sit amet, consectetuer adipiscing elit, sed diam nonummy nibh euismod tincidunt ut laoreet dolore magna aliquam erat volutpat. Ut wisi enim ad minim veniam, quis nostrud exerci tation ullamcorper suscipit lobortis nisl ut aliquip ex ea commodo consequat. Duis autem vel eum iriure dolor in hendiusto odio dignissim qui blandit praesent luptatum zzril delenit augue duis dolore te feugait nulla facilisi.</p>
      <p>Lorem ipsum dolor sit amet, consectetuer adipiscing elit, sed diam nonummy nibh euismod tincidunt ut laoreet dolore magna aliquam erat volutpat. Ut wisi enim ad minim veniam, quis nostrud exerci tation ullamcorper suscipit lobortis nisl ut aliquip ex ea commodo consequat. Duis autem vel eum iriure dolor in hendiusto odio dignissim qui blandit praesent luptatum zzril delenit augue duis dolore te feugait nulla facilisi.</p>
      <p>Lorem ipsum dolor sit amet, consectetuer adipiscing elit, sed diam nonummy nibh euismod tincidunt ut laoreet dolore magna aliquam erat volutpat. Ut wisi enim ad minim veniam, quis nostrud exerci tation ullamcorper suscipit lobortis nisl ut aliquip ex ea commodo consequat. Duis autem vel eum iriure dolor in hendiusto odio dignissim qui blandit praesent luptatum zzril delenit augue duis dolore te feugait nulla facilisi.</p>
    </div>
    <p class="closing">Sincerely Your,</p>
    <p class="signature">Your Name</p>
    <div class="footer-rule"></div>
    <div class="end-mark">Harborline<span class="end-ring"></span></div>
    <p class="footer-address"><svg><use href="#icon-pin"/></svg>Street Name, City Name, Zipcode - 012345</p>
  </section>

  <section class="sheet letter second" aria-label="Letterhead with footer contacts">
    <div class="brand"><span class="brand-ring"></span><span class="brand-name">HARBORLINE</span><span class="brand-sub">REALTY</span></div>
    <p class="salutation">Dear Mr. Lorem,</p>
    <div class="body-copy">
      <p>Lorem ipsum dolor sit amet, consectetuer adipiscing elit, sed diam nonummy nibh euismod tincidunt ut laoreet dolore magna aliquam erat volutpat. Ut wisi enim ad minim veniam, quis nostrud exerci tation ullamcorper suscipit lobortis nisl ut aliquip ex ea commodo consequat. Duis autem vel eum iriure dolor in hendiusto odio dignissim qui blandit praesent luptatum zzril delenit augue duis dolore te feugait nulla facilisi.</p>
      <p>Lorem ipsum dolor sit amet, consectetuer adipiscing elit, sed diam nonummy nibh euismod tincidunt ut laoreet dolore magna aliquam erat volutpat. Ut wisi enim ad minim veniam, quis nostrud exerci tation ullamcorper suscipit lobortis nisl ut aliquip ex ea commodo consequat. Duis autem vel eum iriure dolor in hendiusto odio dignissim qui blandit praesent luptatum zzril delenit augue duis dolore te feugait nulla facilisi.</p>
      <p>Lorem ipsum dolor sit amet, consectetuer adipiscing elit, sed diam nonummy nibh euismod tincidunt ut laoreet dolore magna aliquam erat volutpat. Ut wisi enim ad minim veniam, quis nostrud exerci tation ullamcorper suscipit lobortis nisl ut aliquip ex ea commodo consequat. Duis autem vel eum iriure dolor in hendiusto odio dignissim qui blandit praesent luptatum zzril delenit augue duis dolore te feugait nulla facilisi.</p>
    </div>
    <p class="closing">Sincerely Your,</p>
    <p class="signature">Your Name</p>
    <ul class="contact-list contact-bottom">
      <li><svg><use href="#icon-phone"/></svg>012-345-6789</li>
      <li><svg><use href="#icon-mail"/></svg>info@harborline.com</li>
      <li><svg><use href="#icon-web"/></svg>www.harborline.com</li>
    </ul>
    <div class="footer-rule"></div>
    <div class="end-mark">Harborline<span class="end-ring"></span></div>
    <p class="footer-address"><svg><use href="#icon-pin"/></svg>Street Name, City Name, Zipcode - 012345</p>
  </section>

  <section class="sheet envelope-back" aria-label="Envelope back with navy flap">
    <svg class="flap-fill" viewBox="0 0 360 66" preserveAspectRatio="none"><path d="M0 0H360L352 24Q348 32 336 36L200 64Q180 68 160 64L24 36Q12 32 8 24Z" fill="var(--navy)"/></svg>
    <div class="brand flap-brand"><span class="brand-ring"></span><span class="brand-name">HARBORLINE</span></div>
  </section>

  <section class="sheet envelope-mid" aria-label="Envelope back with open flap">
    <svg class="flap-line" viewBox="0 0 360 70" preserveAspectRatio="none"><path d="M0 0L8 24Q12 32 24 36L160 66Q180 70 200 66L336 36Q348 32 352 24L360 0" fill="none" stroke="var(--rule)" stroke-width="1"/></svg>
    <div class="brand flap-brand" style="color:var(--navy)"><span class="brand-ring"></span><span class="brand-name">HARBORLINE</span></div>
  </section>

  <section class="sheet envelope-front" aria-label="Envelope front">
    <div class="brand"><span class="brand-ring"></span><span class="brand-name">HARBORLINE</span><span class="brand-sub">REALTY</span></div>
    <p class="footer-address"><svg><use href="#icon-pin"/></svg><span>Street Name, City Name<br>Zipcode - 012345</span></p>
    <div class="footer-rule"></div>
    <div class="end-mark">Harborline<span class="end-ring"></span></div>
    <p class="web">www.<strong>harborline</strong>.com</p>
  </section>

  <section class="sheet card-front" aria-label="Business card front">
    <div class="brand"><span class="brand-ring"></span><span class="brand-name">HARBORLINE</span><span class="brand-sub">REALTY</span></div>
    <div class="holder"><p class="holder-name">Dana Whitfield</p><p class="holder-role">President</p></div>
    <ul class="contact-list contact-bottom">
      <li><svg><use href="#icon-phone"/></svg>012-345-6789</li>
      <li><svg><use href="#icon-mail"/></svg>info@harborline.com</li>
    </ul>
    <div class="footer-rule"></div>
    <div class="end-mark"><span class="end-ring"></span></div>
    <p class="footer-address"><svg><use href="#icon-pin"/></svg>Street Name, City Name, Zipcode - 012345</p>
  </section>

  <section class="sheet card-back" aria-label="Business card back">
    <div class="brand"><span class="brand-ring"></span><span class="brand-name">HARBORLINE</span></div>
    <p class="web">www.harborline.com</p>
  </section>

</main>
</body>
</html>
```